2 Page Web Design Project (coded)

What does the company do?
Pilot contracting, flying private/corporate jets.

What is its target market?
The target market is primarily the private jet management market, i.e. companies, which specialize in private aircraft management and are looking to fill crew positions on a short/long term basis, usually on short notice basis

How many pages should your website include?
2 Pages: 1/ Front Page with Company Logo, 2/ Services and Contact page

Do you want coding included? YES

Do you have any style you would like your website to have?
The main colors of my logo should be kept. Please see attached business card logo.

Other Instructions: Please see Veltraxa's website (media section) for Skyrunner 812 pictures for free download, which can be incorporated into the website. Link: http://www.veltraxa.example/en/aerospace/media-centre/multimedia-library/details?categoryID=L3-Veltraxa%20Skyrunner%20812%20Aircraft.

Please see www.midairstaffingdesk.example for services description.
Find attached source file business card and use loge design/font for website, so both business card and website are consistent.

Requirements
Must have
• email link to link to my personal email, without giving my email address.

```html
<!DOCTYPE html>
<html lang="en">
<head>
<meta charset="utf-8">
<title>Northwind Crew Leasing – Services</title>
<link href="https://fonts.googleapis.com/css2?family=Source+Sans+3:wght@400;600&display=swap" rel="stylesheet">
<style>
  :root {
    --page-bg: #e9e9eb;
    --top-bar: #4a4a4b;
    --band: #d8d8d9;
    --frame: #5b5b5c;
    --logo-brown: #3a2a1c;
    --heading-blue: #1a7fc1;
    --text-dark: #1e1e1e;
    --rule: #a9a9a9;
    --panel-border: #d2d2d4;
    --dot: #bdbdbd;
    --dot-active: #e8501c;
    --nav-black: #0c0c0c;
    --nav-divider: #3a3a3a;
    --nav-active: #ff5a1a;
    --footer: #000000;
    --footer-text: #d6d6d6;
  }
  * { box-sizing: border-box; margin: 0; padding: 0; }
  html, body { width: 1200px; height: 1083px; overflow: hidden; }
  body {
    position: relative;
    background: var(--page-bg);
    font-family: "Source Sans 3", "Myriad Pro", Arial, sans-serif;
    color: var(--text-dark);
  }
  .top-bar { position: absolute; left: 0; top: 0; width: 1200px; height: 15px; background: var(--top-bar); }

  .brand {
    position: absolute; left: 162px; top: 92px;
    display: flex; align-items: center; gap: 12px;
    font-size: 30px; font-weight: 400; letter-spacing: 1px;
    color: var(--logo-brown);
  }
  .brand-mark { width: 18px; height: 18px; border-radius: 50%; background: var(--logo-brown); }

  .hero-band { position: absolute; left: 0; top: 171px; width: 1200px; height: 293px; background: var(--band); }
  .hero-frame {
    position: absolute; left: 159px; top: 172px; width: 882px; height: 292px;
    background: var(--frame); border-radius: 6px 6px 2px 2px;
  }
  .hero-shadow {
    position: absolute; left: 175px; top: 488px; width: 855px; height: 30px;
    background: radial-gradient(ellipse at 50% 0%, rgba(0,0,0,.75) 0%, rgba(0,0,0,.35) 45%, rgba(0,0,0,0) 72%);
  }
  .hero-photo {
    position: absolute; left: 170px; top: 181px; width: 858px; height: 309px;
    border-radius: 6px;
    background: linear-gradient(180deg, #7fa9c9 0%, #b9d0e2 35%, #e3ebf1 62%, #c9d3dc 80%, #aab5bf 100%);
  }
  .slider-dots { position: absolute; left: 564px; top: 494px; display: flex; gap: 2px; }
  .slider-dots span { width: 11px; height: 11px; border-radius: 50%; background: var(--dot); box-shadow: inset 0 1px 1px rgba(0,0,0,.2); }
  .slider-dots .is-active { background: var(--dot-active); }

  .content-panel {
    position: absolute; left: 171px; top: 537px; width: 857px; height: 390px;
    border: 1px solid var(--panel-border); border-radius: 8px;
    background: linear-gradient(180deg, #ffffff 0%, #f7f7f8 40%, #ececee 100%);
  }
  .section-title {
    position: absolute; left: 19px; top: 18px;
    font-size: 17px; font-weight: 400; color: var(--heading-blue);
  }
  .section-rule { position: absolute; left: 21px; top: 44px; width: 588px; height: 1px; background: var(--rule); }
  .service-list { position: absolute; left: 49px; top: 75px; list-style: none; }
  .service-list li {
    display: flex; align-items: center; gap: 10px;
    height: 27.7px; font-size: 14.5px; color: var(--text-dark);
  }
  .service-list svg { width: 9px; height: 10px; }
  .service-photo {
    position: absolute; left: 608px; top: 79px; width: 222px; height: 148px;
    border: 1px solid #c4c4c4;
    background: linear-gradient(180deg, #eef0ef 0%, #d8dcda 100%);
  }
  .intro-copy { position: absolute; left: 31px; top: 232px; width: 545px; }
  .intro-copy p {
    font-size: 11.6px; line-height: 19.4px; text-align: justify; margin-bottom: 19.4px;
  }

  .main-nav {
    position: absolute; left: 442px; top: 950px; width: 327px; height: 32px;
    display: flex; background: linear-gradient(180deg, #3a3a3a 0%, var(--nav-black) 35%, var(--nav-black) 100%);
    border-radius: 5px;
  }
  .main-nav a {
    display: flex; align-items: center; justify-content: center;
    color: #ffffff; text-decoration: none; font-size: 12px;
    border-right: 1px solid var(--nav-divider);
  }
  .main-nav a:last-child { border-right: none; }
  .main-nav .nav-home { width: 102px; }
  .main-nav .nav-services { width: 110px; color: var(--nav-active); }
  .main-nav .nav-contact { width: 115px; }
  .nav-shadow {
    position: absolute; left: 445px; top: 980px; width: 321px; height: 12px;
    background: radial-gradient(ellipse at 50% 0%, rgba(0,0,0,.6) 0%, rgba(0,0,0,0) 70%);
  }

  .site-footer {
    position: absolute; left: 0; top: 1003px; width: 1200px; height: 80px;
    background: var(--footer); color: var(--footer-text);
    font-size: 12px; text-align: center; padding-top: 29px;
  }
</style>
</head>
<body>
  <div class="top-bar"></div>

  <header class="brand">
    <span class="brand-mark"></span>
    <span class="brand-name">NORTHWIND CREW LEASING INC</span>
  </header>

  <div class="hero-band"></div>
  <div class="hero-frame"></div>
  <div class="hero-shadow"></div>
  <div class="hero-photo" role="img" aria-label="Business jet parked on a runway apron under a pale blue sky"></div>
  <div class="slider-dots">
    <span></span><span></span><span class="is-active"></span><span></span><span></span><span></span>
  </div>

  <main class="content-panel">
    <h2 class="section-title">What we do:</h2>
    <div class="section-rule"></div>
    <ul class="service-list">
      <li><svg viewBox="0 0 9 10"><path d="M1 1 L7 5 L1 9" fill="none" stroke="#1e1e1e" stroke-width="2"/></svg>Short notice crewing</li>
      <li><svg viewBox="0 0 9 10"><path d="M1 1 L7 5 L1 9" fill="none" stroke="#1e1e1e" stroke-width="2"/></svg>Short term/long term crewing</li>
      <li><svg viewBox="0 0 9 10"><path d="M1 1 L7 5 L1 9" fill="none" stroke="#1e1e1e" stroke-width="2"/></svg>Permanent crew placement/hiring support</li>
      <li><svg viewBox="0 0 9 10"><path d="M1 1 L7 5 L1 9" fill="none" stroke="#1e1e1e" stroke-width="2"/></svg>Aircraft ferry</li>
      <li><svg viewBox="0 0 9 10"><path d="M1 1 L7 5 L1 9" fill="none" stroke="#1e1e1e" stroke-width="2"/></svg>New/pre-owned aircraft delivery</li>
    </ul>
    <div class="service-photo" role="img" aria-label="Passenger jet in flight seen from below against an overcast sky"></div>
    <div class="intro-copy">
      <p>Northwind Crew Leasing is a service provider to the Business Aviation community, providing qualified pilots for aircraft owners and operators, flying the Veltraxa Skyrunner series of aircraft.</p>
      <p>At Northwind Crew Leasing we exclusively focus on the needs of the Business Aviation market and it s discerning clients. We demand the best of our crew, who are tasked in providing short/long term crewing. All our crews have multiple years experience in the VVIP market, are highly qualified and come from various backgrounds including Military, Airline and Instruction.</p>
    </div>
  </main>

  <div class="nav-shadow"></div>
  <nav class="main-nav">
    <a class="nav-home" href="#">Home</a>
    <a class="nav-services" href="#">Services</a>
    <a class="nav-contact" href="#">Contact Us</a>
  </nav>

  <footer class="site-footer">Copyrights @ 2012 All Rights Reserved</footer>
</body>
</html>
```